Sale PPC Banner Ad Design Update

We need some Google PPC Banner Ad's for our sale altered to include product shots in the background. Attached are some examples that we currently use. We want a similar format/look but with the attached product shots used as the background image. Product image is called "KTPOle Grade 4"

Have also included our logo file as well.

Industry/Entity Type

Google

Font styles to use
Sans Serif

Requirements
Must have
• The must-have sizes (up to 150kb):
• • Banner: 468 x 60
• • Large mobile banner 320 x 100
• • Leaderboard: 728 x 90
• • Square: 250 x 250
• • Small square: 200 x 200
• • Large rectangle: 336 x 280
Nice to have
• The nice-to-have sizes:
• • Vertical rectangle: 240 x 400
• • Mobile leaderboard: 320 x 50
• • Inline rectangle: 300 x 250
• • Skyscraper: 120 x 600
• • Wide skyscraper: 160 x 600
• • Half-page: 300 x 600
• • Large leaderboard: 970 x 90
• • Billboard: 970 x 250
• • Portrait: 300 x 1050

```html
<!DOCTYPE html>
<html lang="en">
<head>
<meta charset="UTF-8">
<title>KTPOle Grade 4 – Sale Leaderboard</title>
<link rel="stylesheet" href="https://fonts.googleapis.com/css2?family=Montserrat:wght@300;400;600&display=swap">
<style>
  :root {
    --paper: #ffffff;
    --ink: #111111;
    --sale-red: #e8354a;
    --cta-white: #ffffff;
    --rug-deep: #2a121e;
    --rug-red: #7c1a34;
    --rug-plum: #4a1d4f;
    --rug-ochre: #6b4a1a;
  }
  * { margin: 0; padding: 0; box-sizing: border-box; }
  html, body {
    width: 1200px;
    height: 148px;
    overflow: hidden;
    background: var(--paper);
  }
  .banner {
    position: relative;
    width: 1200px;
    height: 148px;
    display: flex;
    font-family: "Montserrat", sans-serif;
  }
  .brand-strip {
    position: relative;
    width: 53px;
    height: 148px;
    background: var(--paper);
    flex: none;
  }
  .brand-name {
    position: absolute;
    left: 50%;
    bottom: 8px;
    transform-origin: left bottom;
    transform: translateX(13px) rotate(-90deg);
    font-family: "Montserrat", sans-serif;
    font-weight: 400;
    font-size: 27px;
    line-height: 1;
    color: var(--ink);
    white-space: nowrap;
  }
  .product-photo {
    position: relative;
    flex: 1;
    height: 148px;
    background:
      linear-gradient(180deg, rgba(20, 8, 14, 0.55) 0%, rgba(20, 8, 14, 0.1) 45%, rgba(20, 8, 14, 0.25) 100%),
      linear-gradient(90deg, var(--rug-red) 0%, var(--rug-plum) 22%, var(--rug-deep) 40%, var(--rug-red) 55%, var(--rug-plum) 72%, var(--rug-ochre) 86%, var(--rug-red) 100%);
  }
  .offer {
    position: absolute;
    left: 593px;
    top: 0;
    height: 148px;
    transform: translateX(-50%);
    display: flex;
    flex-direction: column;
    align-items: center;
    justify-content: center;
  }
  .offer-title {
    font-weight: 300;
    font-size: 46px;
    letter-spacing: 7px;
    padding-left: 7px;
    color: var(--sale-red);
    line-height: 1;
    margin-top: -4px;
  }
  .offer-cta {
    margin-top: 16px;
    font-weight: 600;
    font-size: 16px;
    letter-spacing: 2.5px;
    padding-left: 2.5px;
    color: var(--cta-white);
    line-height: 1;
  }
</style>
</head>
<body>
  <div class="banner">
    <div class="brand-strip">
      <span class="brand-name">KTPOle</span>
    </div>
    <div class="product-photo" role="img" aria-label="KTPOle Grade 4 loafers in black and white leather worn on a red, purple and yellow patterned rug"></div>
    <div class="offer">
      <span class="offer-title">SALE</span>
      <span class="offer-cta">SHOP NOW</span>
    </div>
  </div>
</body>
</html>
```